MES Modul-Struktur grafisch veranschaulichen
Zielgruppe
Wir sind Software-Hersteller. Thema 'MES'. Unsere Kunden sind Produktionsunternehmen.
Mit einem MES (Manufacturing Execution System) werden Produktionsprozesse überwacht, geplant, gesteuert und optimiert. Allgemein geht es darum, die Produktivität zu steigern und Kosten zu minimieren.
Eine MES-Software ist modular strukturiert, so dass der Kunde sich nach Bedarf die einzelnen Funktionsmodule zusammenstellen kann. Unser MES KORVIN 7 MAX besteht z.B. aus folgenden Einzelmodulen:
- BASIS (Basismodul)
- MDE (Maschinendatenerfassung)
- BDE (Betriebsdatenerfassung)
- INST (Instandhaltung)
- ALARM (Alarmierung)
- DOK (Dokumentenmanagement)
- TNT (Traceability)
- PLAN (Feinplanung/Leitstand)
- LOG (Logistik)
- VIS (Visualisierung)
- PEP (Personaleinsatzplanung)
- MPZE (Personalzeiterfassung)
- DNC (Rezepturen/DNC)
- EM (Energiemonitoring)
Aufgabenstellung
Die modulare Struktur und der große Umfang an Modulen ist ein wichtiger Vorteil für unsere Kunden, da Sie nicht so schnell an Grenzen stoßen und sich dann unter Umständen eine weitere Insellösung (extra Software mit extra Datenbank ...) anschaffen müssen.
Wichtig ist, dass die einzelnen Module funktionell ineinandergreifen und alle auf die gleiche Datenbank zugreifen.
Es reicht wenn in der Grafik die Module nur mit er Abkürzung, also z.B. MDE bezeichnet werden. Für den ersten Entwurf können auch Platzhalter genutzt werden.
Der Betrachter sollte aus der Grafik auf den ersten Blick erkennen:
- umfängliches MES
- modular strukturiert
- Funktionsmodule step-by-step erweiterbar
Für die Umsetzung naheliegend wären Puzzle-Steine, Blokkis, ... muss aber nicht.

```html
<!DOCTYPE html>
<html lang="de">
<head>
<meta charset="utf-8">
<title>MES Module</title>
<link rel="stylesheet" href="https://fonts.googleapis.com/css2?family=Roboto+Condensed:wght@400;700&display=swap">
<style>
  :root{
    --canvas:#e3e6e9;
    --white:#ffffff;
    --tone-em:#1f9e9a;
    --tone-dnc:#2387b5;
    --tone-mpze:#2f6db5;
    --tone-pep:#4a56a8;
    --tone-vis:#6b4a9e;
    --tone-log:#8f3f8f;
    --tone-plan:#b23a6d;
    --tone-tnt:#cf4a4a;
    --tone-dok:#e0683a;
    --tone-alarm:#e88f2c;
    --tone-inst:#d9a520;
    --tone-bde:#8fae35;
    --tone-mde:#4f9f52;
    --tone-basis:#56636f;
  }
  *{margin:0;padding:0;box-sizing:border-box}
  html,body{width:848px;height:1200px;overflow:hidden}
  body{background:var(--canvas);font-family:"Roboto Condensed",Arial,sans-serif}
  .shared-defs{position:absolute;width:0;height:0}
  .module-stack{position:relative;width:848px;height:1200px}
  .module{position:absolute;width:216px;height:104px}
  .module--left{left:214px}
  .module--right{left:423px}
  .module__shape{position:absolute;inset:0;width:216px;height:104px;overflow:visible;filter:drop-shadow(0 1px 2px rgba(0,0,0,.14))}
  .shape-frame{fill:var(--white)}
  .shape-fill{fill:var(--tone)}
  .shape-sheen{fill:url(#tag-sheen)}
  .badge-ring{fill:var(--tone)}
  .badge-core{fill:var(--white)}
  .icon{fill:none;stroke:var(--tone);stroke-width:3;stroke-linecap:round;stroke-linejoin:round}
  .icon .solid{fill:var(--tone);stroke:none}
  .module__label{position:absolute;top:16px;color:var(--white)}
  .module--left .module__label{left:88px;text-align:left}
  .module--right .module__label{right:88px;text-align:right}
  .module__code{display:block;font-weight:700;font-size:23px;line-height:28px;letter-spacing:.2px}
  .module__name{display:block;margin-top:6px;font-size:12px;line-height:14px}

  .module--em{--tone:var(--tone-em)}
  .module--dnc{--tone:var(--tone-dnc)}
  .module--mpze{--tone:var(--tone-mpze)}
  .module--pep{--tone:var(--tone-pep)}
  .module--vis{--tone:var(--tone-vis)}
  .module--log{--tone:var(--tone-log)}
  .module--plan{--tone:var(--tone-plan)}
  .module--tnt{--tone:var(--tone-tnt)}
  .module--dok{--tone:var(--tone-dok)}
  .module--alarm{--tone:var(--tone-alarm)}
  .module--inst{--tone:var(--tone-inst)}
  .module--bde{--tone:var(--tone-bde)}
  .module--mde{--tone:var(--tone-mde)}
  .module--basis{--tone:var(--tone-basis)}
</style>
</head>
<body>
<svg class="shared-defs" aria-hidden="true">
  <defs>
    <linearGradient id="tag-sheen" x1="0" y1="0" x2="0.35" y2="1">
      <stop offset="0" stop-color="#fff" stop-opacity=".16"/>
      <stop offset="1" stop-color="#000" stop-opacity=".14"/>
    </linearGradient>
    <symbol id="tag" viewBox="0 0 216 104">
      <polygon class="shape-frame" points="28,0 196,0 216,52 196,104 28,104"/>
      <polygon class="shape-fill" points="30,6 192,6 210,52 192,98 30,98"/>
      <polygon class="shape-sheen" points="30,6 192,6 210,52 192,98 30,98"/>
      <circle class="shape-frame" cx="43" cy="52" r="42"/>
      <circle class="badge-ring" cx="43" cy="52" r="35"/>
      <circle class="badge-core" cx="43" cy="52" r="29"/>
    </symbol>
  </defs>
</svg>

<main class="module-stack">

  <div class="module module--left module--em" style="top:55px">
    <svg class="module__shape" viewBox="0 0 216 104" aria-hidden="true">
      <use href="#tag" width="216" height="104"/>
      <g class="icon" transform="translate(43 52)">
        <path class="solid" d="M3 -16 L-9 2 H-1 L-4 16 L9 -3 H1 Z"/>
      </g>
    </svg>
    <div class="module__label"><span class="module__code">EM</span><span class="module__name">Energie-<br>monitoring</span></div>
  </div>

  <div class="module module--right module--dnc" style="top:130px">
    <svg class="module__shape" viewBox="0 0 216 104" aria-hidden="true">
      <use href="#tag" width="216" height="104" transform="translate(216 0) scale(-1 1)"/>
      <g class="icon" transform="translate(173 52)">
        <rect x="-12" y="-14" width="24" height="28" rx="2"/>
        <path d="M-6 -6 H6 M-6 0 H6 M-6 6 H2"/>
      </g>
    </svg>
    <div class="module__label"><span class="module__code">DNC</span><span class="module__name">Rezepturen/DNC</span></div>
  </div>

  <div class="module module--left module--mpze" style="top:205px">
    <svg class="module__shape" viewBox="0 0 216 104" aria-hidden="true">
      <use href="#tag" width="216" height="104"/>
      <g class="icon" transform="translate(43 52)">
        <path d="M-10 -15 H10 M-10 15 H10"/>
        <path d="M-8 -15 C-8 -4 8 4 8 15 M8 -15 C8 -4 -8 4 -8 15"/>
      </g>
    </svg>
    <div class="module__label"><span class="module__code">MPZE</span><span class="module__name">Personalzeit-<br>erfassung</span></div>
  </div>

  <div class="module module--right module--pep" style="top:279px">
    <svg class="module__shape" viewBox="0 0 216 104" aria-hidden="true">
      <use href="#tag" width="216" height="104" transform="translate(216 0) scale(-1 1)"/>
      <g class="icon" transform="translate(173 52)">
        <circle cx="-6" cy="-7" r="5"/>
        <path d="M-15 12 C-15 2 3 2 3 12"/>
        <circle cx="8" cy="-5" r="4"/>
        <path d="M7 4 C12 3 16 6 16 12"/>
      </g>
    </svg>
    <div class="module__label"><span class="module__code">PEP</span><span class="module__name">Personaleinsatz-<br>planung</span></div>
  </div>

  <div class="module module--left module--vis" style="top:354px">
    <svg class="module__shape" viewBox="0 0 216 104" aria-hidden="true">
      <use href="#tag" width="216" height="104"/>
      <g class="icon" transform="translate(43 52)">
        <rect x="-15" y="-12" width="30" height="20" rx="2"/>
        <path d="M-6 14 H6 M0 8 V14"/>
      </g>
    </svg>
    <div class="module__label"><span class="module__code">VIS</span><span class="module__name">Visualisierung</span></div>
  </div>

  <div class="module module--right module--log" style="top:429px">
    <svg class="module__shape" viewBox="0 0 216 104" aria-hidden="true">
      <use href="#tag" width="216" height="104" transform="translate(216 0) scale(-1 1)"/>
      <g class="icon" transform="translate(173 52)">
        <path d="M0 -15 L14 -8 V8 L0 15 L-14 8 V-8 Z"/>
        <path d="M-14 -8 L0 -1 L14 -8 M0 -1 V15"/>
      </g>
    </svg>
    <div class="module__label"><span class="module__code">LOG</span><span class="module__name">Logistik</span></div>
  </div>

  <div class="module module--left module--plan" style="top:504px">
    <svg class="module__shape" viewBox="0 0 216 104" aria-hidden="true">
      <use href="#tag" width="216" height="104"/>
      <g class="icon" transform="translate(43 52)">
        <path d="M-15 -14 V14"/>
        <rect class="solid" x="-11" y="-12" width="14" height="5" rx="1"/>
        <rect class="solid" x="-5" y="-3" width="16" height="5" rx="1"/>
        <rect class="solid" x="2" y="6" width="13" height="5" rx="1"/>
      </g>
    </svg>
    <div class="module__label"><span class="module__code">PLAN</span><span class="module__name">Feinplanung/<br>Leitstand</span></div>
  </div>

  <div class="module module--right module--tnt" style="top:579px">
    <svg class="module__shape" viewBox="0 0 216 104" aria-hidden="true">
      <use href="#tag" width="216" height="104" transform="translate(216 0) scale(-1 1)"/>
      <g class="icon" transform="translate(173 52)">
        <circle class="solid" cx="-12" cy="10" r="4"/>
        <circle class="solid" cx="12" cy="-10" r="4"/>
        <path d="M-12 10 H0 V-10 H12" style="stroke-dasharray:3 3"/>
      </g>
    </svg>
    <div class="module__label"><span class="module__code">TNT</span><span class="module__name">Traceability</span></div>
  </div>

  <div class="module module--left module--dok" style="top:653px">
    <svg class="module__shape" viewBox="0 0 216 104" aria-hidden="true">
      <use href="#tag" width="216" height="104"/>
      <g class="icon" transform="translate(43 52)">
        <path d="M-15 -11 H-5 L-1 -7 H15 V12 H-15 Z"/>
        <path d="M-15 -3 H15"/>
      </g>
    </svg>
    <div class="module__label"><span class="module__code">DOK</span><span class="module__name">Dokumenten-<br>management</span></div>
  </div>

  <div class="module module--right module--alarm" style="top:728px">
    <svg class="module__shape" viewBox="0 0 216 104" aria-hidden="true">
      <use href="#tag" width="216" height="104" transform="translate(216 0) scale(-1 1)"/>
      <g class="icon" transform="translate(173 52)">
        <path d="M-11 8 V-2 A11 11 0 0 1 11 -2 V8 L14 11 H-14 Z"/>
        <path d="M-4 14 A4 4 0 0 0 4 14 M0 -13 V-15"/>
      </g>
    </svg>
    <div class="module__label"><span class="module__code">ALARM</span><span class="module__name">Alarmierung</span></div>
  </div>

  <div class="module module--left module--inst" style="top:803px">
    <svg class="module__shape" viewBox="0 0 216 104" aria-hidden="true">
      <use href="#tag" width="216" height="104"/>
      <g class="icon" transform="translate(43 52)">
        <circle r="10" style="stroke-width:6;stroke-dasharray:5 3.4"/>
        <circle r="5"/>
      </g>
    </svg>
    <div class="module__label"><span class="module__code">INST</span><span class="module__name">Instandhaltung</span></div>
  </div>

  <div class="module module--right module--bde" style="top:878px">
    <svg class="module__shape" viewBox="0 0 216 104" aria-hidden="true">
      <use href="#tag" width="216" height="104" transform="translate(216 0) scale(-1 1)"/>
      <g class="icon" transform="translate(173 52)">
        <path d="M-15 -13 V13 H15"/>
        <path d="M-10 6 L-3 -2 L3 3 L13 -9"/>
      </g>
    </svg>
    <div class="module__label"><span class="module__code">BDE</span><span class="module__name">Betriebsdaten-<br>erfassung</span></div>
  </div>

  <div class="module module--left module--mde" style="top:953px">
    <svg class="module__shape" viewBox="0 0 216 104" aria-hidden="true">
      <use href="#tag" width="216" height="104"/>
      <g class="icon" transform="translate(43 52)">
        <path d="M-15 13 V-3 L-6 -9 V-3 L3 -9 V-3 L15 -11 V13 Z"/>
        <rect class="solid" x="-10" y="4" width="5" height="5"/>
        <rect class="solid" x="0" y="4" width="5" height="5"/>
      </g>
    </svg>
    <div class="module__label"><span class="module__code">MDE</span><span class="module__name">Maschinendaten-<br>erfassung</span></div>
  </div>

  <div class="module module--right module--basis" style="top:1027px">
    <svg class="module__shape" viewBox="0 0 216 104" aria-hidden="true">
      <use href="#tag" width="216" height="104" transform="translate(216 0) scale(-1 1)"/>
      <g class="icon" transform="translate(173 52)">
        <ellipse cx="0" cy="-10" rx="12" ry="5"/>
        <path d="M-12 -10 V10 A12 5 0 0 0 12 10 V-10"/>
        <path d="M-12 0 A12 5 0 0 0 12 0"/>
      </g>
    </svg>
    <div class="module__label"><span class="module__code">BASIS</span><span class="module__name">Basismodul</span></div>
  </div>

</main>
</body>
</html>
```